Business Cards - Brightpath Horizon

need to design unique business card for my mortgage business. I need to design credit card style business card for my business or any unique idea that you might have

Target Market(s)

Home Loan customers

Industry/Entity Type

Mortgage Brokerage

Contact Information for Business Card

please design credit card style or very unique style business card

Colors

Designer to choose colors to be used in the design.

Requirements
Must have
• Name
• position
• Phone number
• fax number
• email address
• website address
• social media address
• All above fields will be provided once design in finalised

```html
<!DOCTYPE html>
<html lang="en">
<head>
<meta charset="utf-8">
<title>Brightpath Horizon — Business Card</title>
<link rel="stylesheet" href="https://fonts.googleapis.com/css2?family=Arimo:wght@400;700&family=Roboto+Slab:wght@700&family=Share+Tech+Mono&display=swap">
<style>
  :root {
    --backdrop: #d8d2ca;
    --card-dark: #0b0b0d;
    --card-mid: #1d1e22;
    --brand-blue: #2f5cb8;
    --brand-dot: #e07a2e;
    --contact-light: #d9d9d9;
    --number-gold: #c9a45a;
    --name-teal: #3a86a8;
    --title-rose: #b89a92;
    --social-dot: #2c5e86;
    --web-blue: #2e78b5;
  }
  * { margin: 0; padding: 0; box-sizing: border-box; }
  html, body {
    width: 1200px; height: 969px; overflow: hidden;
    background: var(--backdrop);
  }
  .canvas {
    position: relative; width: 1200px; height: 969px;
    display: flex; align-items: center; justify-content: center;
  }
  .card {
    position: relative; width: 900px; height: 516px;
    border-radius: 30px;
    background:
      radial-gradient(ellipse at 45% 40%, var(--card-mid) 0%, var(--card-dark) 70%);
    box-shadow: 0 18px 40px rgba(0,0,0,0.25);
    font-family: "Arimo", Arial, sans-serif;
  }
  .brand {
    position: absolute; left: 44px; top: 56px;
    display: flex; align-items: center; gap: 14px;
  }
  .brand-dot {
    width: 26px; height: 26px; border-radius: 50%;
    background: var(--brand-dot);
  }
  .brand-name {
    font-family: "Roboto Slab", Georgia, serif; font-weight: 700;
    color: var(--brand-blue); font-size: 30px; line-height: 1.05;
    text-transform: uppercase; letter-spacing: 1px;
  }
  .contact {
    position: absolute; right: 40px; top: 74px;
    text-align: right; color: var(--contact-light);
    font-size: 22px; line-height: 32px; letter-spacing: 0.5px;
  }
  .card-number {
    position: absolute; left: 0; right: 0; top: 248px;
    text-align: center;
    font-family: "Share Tech Mono", monospace;
    font-size: 58px; line-height: 70px; letter-spacing: 10px; word-spacing: 24px;
    color: var(--number-gold);
    text-shadow: 0 1px 0 rgba(0,0,0,0.6);
  }
  .holder {
    position: absolute; left: 40px; top: 392px;
    font-family: "Roboto Slab", Georgia, serif; font-weight: 700;
    text-transform: uppercase;
  }
  .holder-name { color: var(--name-teal); font-size: 27px; line-height: 36px; }
  .holder-title { color: var(--title-rose); font-size: 21px; line-height: 34px; }
  .social {
    position: absolute; right: 40px; top: 388px;
    display: flex; gap: 8px;
  }
  .social-dot {
    width: 38px; height: 38px; border-radius: 50%;
    background: var(--social-dot);
  }
  .website {
    position: absolute; right: 40px; top: 434px;
    color: var(--web-blue); font-size: 20px; line-height: 24px; letter-spacing: 2px;
  }
</style>
</head>
<body>
<main class="canvas">
  <section class="card">
    <div class="brand">
      <span class="brand-dot"></span>
      <div class="brand-name">Brightpath<br>Horizon</div>
    </div>

    <div class="contact">
      <div class="contact-phone">P. 555 210 4821</div>
      <div class="contact-email">hello@brightpathhz.com</div>
    </div>

    <div class="card-number">730 415 0086</div>

    <div class="holder">
      <div class="holder-name">Daniel Reyes</div>
      <div class="holder-title">CEO/Founder</div>
    </div>

    <div class="social" aria-label="Social media links">
      <span class="social-dot"></span>
      <span class="social-dot"></span>
      <span class="social-dot"></span>
      <span class="social-dot"></span>
    </div>
    <div class="website">www.brightpathhz.com</div>
  </section>
</main>
</body>
</html>
```